WP website design (Tarnwick)

We need a wordpress design for an established auction and real estate company based in Arkansas. The winning design will incorporate a professional color scheme with company logo in a clean layout. The design needs to consider that this will be developed on a responsive theme.

Industry/Entity Type

Real Estate

Font styles to use
Sans Serif

Colors

Designer to choose colors to be used in the design.

Requirements
Must have
• Site will have slideshow, please use stock real estate or other image. A rough idea of homepage content is attached - not necessarily for design purposes.

Navigation Structure is:
1) Home
2) Auctions
3) Services
4) For Sale
5) About Us
6) Ned Videos
7) News & Events
8) Contact Us

Widgets will include:
Social media icons (Facebook, Youtube, RSS)
Testimonials Widget - this should be prominent
Featured Video
Email Signup form (Sign up to receive exclusive email updates for Tarnwick auctions. )
Nice to have
• A drop down menu example
Should not have
• no gavel in the design

```html
<!DOCTYPE html>
<html lang="en">
<head>
<meta charset="utf-8">
<title>Tarnwick Auction &amp; Marketing</title>
<link rel="stylesheet" href="https://fonts.googleapis.com/css2?family=Cinzel:wght@400;700&family=Arimo:wght@400;700&family=Open+Sans:ital,wght@0,400;1,400&display=swap">
<style>
:root{
  --ink:#231f20;
  --green:#00843d;
  --brown:#6b5a3c;
  --text:#1a1a1a;
  --field:#f1f1f1;
  --white:#fff;
}
*{box-sizing:border-box;margin:0;padding:0}
html,body{width:1137px;height:1200px;overflow:hidden;background:var(--white)}
body{position:relative;font-family:"Arimo",Arial,sans-serif;color:var(--text)}
.abs{position:absolute}

/* header */
.brand{left:106px;top:34px;display:flex;align-items:center;gap:12px}
.brand-dot{width:34px;height:34px;border-radius:50%;background:var(--green)}
.brand-text{font-family:"Arimo",Arial,sans-serif;font-weight:700;color:var(--ink);line-height:1.15}
.brand-text .n{font-size:34px;letter-spacing:.5px}
.brand-text .s{font-size:15px}
.social{left:865px;top:45px;display:flex;gap:5px}
.social span{width:32px;height:32px;border-radius:50%;border:1px solid #bdbdbd;background:linear-gradient(#fff,#eee)}

/* navigation */
.nav{left:0;top:124px;width:1137px;height:45px;background:var(--ink);border-bottom:1px solid #555}
.nav ul{list-style:none;display:flex;position:absolute;left:96px;top:4px;height:36px;align-items:center}
.nav li{font-family:"Cinzel",serif;font-size:14px;color:var(--white);padding:0 24px;height:32px;line-height:32px;letter-spacing:.3px}
.nav li.active{background:#111;border:1px solid #4a4a4a;border-radius:3px;padding:0 18px;margin-right:6px}

/* hero */
.hero{left:0;top:169px;width:1137px;height:450px}
.welcome{left:0;top:544px;width:1137px;text-align:center;font-family:"Cinzel",serif;font-size:35px;color:var(--ink);letter-spacing:1px;padding-left:90px}

/* listings */
.section-title{left:114px;top:638px;font-family:"Cinzel",serif;font-size:19px;color:var(--ink);letter-spacing:.5px}
.listing{left:114px;width:605px;height:170px}
.thumb{left:0;top:0;width:106px;height:82px;border:1px solid #ddd;padding:2px;background:#fff}
.thumb div{width:100%;height:100%;background:linear-gradient(#dfe9f2 0%,#c7cdd6 45%,#5f8f3a 60%,#4a7a2c 100%)}
.btn{left:2px;width:104px;height:28px;border-radius:4px;color:#fff;font-weight:700;font-size:13px;display:flex;align-items:center;justify-content:center;gap:10px}
.btn.details{top:91px;background:linear-gradient(#3f8e5c,#1f6a3c)}
.btn.photos{top:129px;background:linear-gradient(#555,#222)}
.btn i{display:inline-block;width:16px;height:11px;border:2px solid #fff;border-radius:2px}
.info{left:116px;top:0;width:489px;font-size:12px;line-height:19px}
.kind{font-weight:700;font-size:13px;color:var(--brown);letter-spacing:.6px;margin-top:2px}
.desc{margin-top:14px;text-align:justify;line-height:17px}

.divider{left:755px;top:641px;width:0;height:455px;border-left:1px dashed #cfcfcf}

/* sidebar */
.side-title{font-family:"Cinzel",serif;font-size:19px;color:var(--green);letter-spacing:.5px}
.field{left:780px;width:243px;height:32px;border-radius:16px;background:var(--field);border:1px solid #ddd;box-shadow:inset 0 2px 2px rgba(0,0,0,.12);font-size:13px;color:#333;padding:8px 16px}
.signup{left:915px;top:820px;width:105px;height:32px;border-radius:5px;background:linear-gradient(#3f8e5c,#1c6538);color:#fff;font-family:"Cinzel",serif;font-size:16px;text-align:center;line-height:32px}
.quote{left:786px;top:910px;width:234px;font-family:"Open Sans",sans-serif;font-size:11px;line-height:15.2px;color:#333}
.quote b{font-family:Georgia,serif;font-size:18px;color:#555;line-height:0;vertical-align:-4px}
.byline{right:192px;top:1030px;text-align:right;font-family:"Open Sans",sans-serif;font-style:italic;font-size:11px;line-height:19px}
.byline .date{color:var(--green)}
.avatar{left:962px;top:1024px;width:50px;height:42px;border:1px solid #ddd;padding:2px;background:#fff}
.avatar div{width:100%;height:100%;background:linear-gradient(#e8b48c,#c98a5e)}

/* footer */
.footer{left:0;top:1107px;width:1137px;height:93px;background:var(--ink);color:#e6e6e6;font-size:12px;line-height:21px}
.footer .addr{position:absolute;left:112px;top:16px}
.footer .brand-f{position:absolute;right:118px;top:24px;text-align:right;font-family:"Arimo",Arial,sans-serif;font-weight:700;color:#fff;line-height:1.2}
.footer .brand-f .n{font-size:24px}
.footer .brand-f .s{font-size:11px}
</style>
</head>
<body>

<header>
  <div class="abs brand">
    <div class="brand-dot"></div>
    <div class="brand-text"><div class="n">Tarnwick</div><div class="s">Auction &amp; Marketing, LLC</div></div>
  </div>
  <div class="abs social" aria-label="Social media links">
    <span></span><span></span><span></span><span></span><span></span>
  </div>
</header>

<nav class="abs nav">
  <ul>
    <li class="active">HOME</li><li>AUCTIONS</li><li>SERVICES</li><li>FOR SALE</li><li>ABOUT US</li><li>NED VIDEOS</li><li>NEWS &amp; EVENTS</li><li>CONTACT US</li>
  </ul>
</nav>

<section class="abs hero">
  <svg width="1137" height="450" viewBox="0 0 1137 450">
    <defs>
      <linearGradient id="band" x1="0" x2="1">
        <stop offset="0" stop-color="#00a04e"/><stop offset=".5" stop-color="#009a4b"/><stop offset="1" stop-color="#006e32"/>
      </linearGradient>
      <linearGradient id="house" x1="0" y1="0" x2="0" y2="1">
        <stop offset="0" stop-color="#eef1f2"/><stop offset=".35" stop-color="#8b949a"/><stop offset=".7" stop-color="#b9c0bd"/><stop offset="1" stop-color="#d7d9d5"/>
      </linearGradient>
      <linearGradient id="arc" x1="0" y1="0" x2="0" y2="1">
        <stop offset="0" stop-color="#ffffff"/><stop offset="1" stop-color="#e9e9e9"/>
      </linearGradient>
    </defs>
    <path d="M0 0H1137V450Q568 410 0 450Z" fill="url(#band)"/>
    <rect x="101" y="4" width="935" height="425" fill="url(#house)" role="img" aria-label="Slideshow photo of a large two-storey family home with a wrap-around porch"/>
    <path d="M101 405Q568 292 1036 405" fill="none" stroke="#00843d" stroke-width="6"/>
    <path d="M101 408Q568 296 1036 408V440H101Z" fill="url(#arc)"/>
    <path d="M0 450Q568 410 1137 450Z" fill="#fff"/>
    <path d="M30 436Q568 400 1107 436L1137 450Q568 410 0 450Z" fill="url(#arc)"/>
  </svg>
</section>
<h1 class="abs welcome">WELCOME TO TARNWICK</h1>

<main>
  <h2 class="abs section-title">Shop Equipment/Tools * Pork Processing Items</h2>

  <article class="abs listing" style="top:685px">
    <div class="abs thumb"><div role="img" aria-label="Photo of an auction crowd in front of a white house"></div></div>
    <div class="abs btn details"><i></i>Details</div>
    <div class="abs btn photos"><i></i>Photos</div>
    <div class="abs info">
      <div class="kind">LIVE ON-SITE AUCTION</div>
      <div><b>Begins:</b>&nbsp; Saturday, March 16, 2013 at 10:00 AM EDT</div>
      <div><b>Location:</b>&nbsp; 2150 Millrace Road Alder Falls, KY 40990</div>
      <p class="desc">Koroda BS3F High Lift, simply dummy text of the printing and typesetting industry simply dummy text of the printing and typesetting industry 600 Series Halden tractor w/Bramwell Loader, Dune buggy, 1207 HK Cutditioner: SHOP &amp; MISCELLANIOUS &amp; PORK PROCESS-ING ITEMS.</p>
    </div>
  </article>

  <article class="abs listing" style="top:871px">
    <div class="abs thumb"><div role="img" aria-label="Photo of an auction crowd in front of a white house"></div></div>
    <div class="abs btn details"><i></i>Details</div>
    <div class="abs btn photos"><i></i>Photos</div>
    <div class="abs info">
      <div class="kind">LIVE ON-SITE AUCTION</div>
      <div><b>Begins:</b>&nbsp; Saturday, March 16, 2013 at 10:00 AM EDT</div>
      <div><b>Location:</b>&nbsp; 2150 Millrace Road Alder Falls, KY 40990</div>
      <p class="desc">Koroda BS3F High Lift, simply dummy text of the printing and typesetting industry simply dummy text of the printing and typesetting industry 600 Series Halden tractor w/Bramwell Loader, Dune buggy, 1207 HK Cutditioner: SHOP &amp; MISCELLANIOUS &amp; PORK PROCESS-ING ITEMS.</p>
    </div>
  </article>

  <div class="abs divider"></div>
</main>

<aside>
  <h3 class="abs side-title" style="left:782px;top:634px">Email Sign Up</h3>
  <div class="abs field" style="top:672px">First Name</div>
  <div class="abs field" style="top:721px">Last Name</div>
  <div class="abs field" style="top:773px">Email Address</div>
  <div class="abs signup">SIGN UP</div>

  <h3 class="abs side-title" style="left:786px;top:874px">Client Testimonials</h3>
  <p class="abs quote"><b>“</b> simply dummy text of the printing and typesetting industry. Lorem Ipsum has been the simply dummy text of the printing and typesetting industry. Lorem Ipsum has been the simply dummy text of the printing and been the simplytypesetting industry. <b>”</b></p>
  <div class="abs byline">By Owen Barley<br><span class="date">Posted on Nov25, 2013</span></div>
  <div class="abs avatar"><div role="img" aria-label="Portrait photo of the client"></div></div>
</aside>

<footer class="abs footer">
  <div class="addr">Tarnwick and Company Auctioneers<br>418 Linden Avenue NE • Brookvale, FL 33990<br>P: 555-014-7867 • F: 555-014-7869 • info@tarnwickauctioneers.example</div>
  <div class="brand-f"><div class="n">Tarnwick</div><div class="s">Auction &amp; Marketing, LLC</div></div>
</footer>

</body>
</html>
```